Redesign current business card for food company

i would like to redesign my business card. our company is food company, our product range from chips, juices, milk and etc (mostly dried food stuff).
I want o keep same logo but , the rest is open to new design.
you can check at our website about our company www.orvelpantry.com

Target Market(s)

most of food company

Industry/Entity Type

Business

Contact Information for Business Card

I want to keep more to blue color...

Colors
3176b5
abd036

Requirements
Must have
• our old logo
Nice to have
• we do not mind to have nice material on bus card in order to accomplish nice design. for example: using spot uv, embossed and etc.

```html
<!DOCTYPE html>
<html lang="en">
<head>
<meta charset="utf-8">
<title>Orvel Business Card</title>
<link rel="stylesheet" href="https://fonts.googleapis.com/css2?family=Ubuntu:wght@400;500&display=swap">
<style>
  :root {
    --backdrop: #222222;
    --navy: #2e3192;
    --indigo: #33348f;
    --brand-blue: #3176b5;
    --cyan: #04aac9;
    --green: #3db54a;
    --green-light: #abd036;
    --ink: #111111;
    --paper: #ffffff;
  }
  * { margin: 0; padding: 0; box-sizing: border-box; }
  html, body {
    width: 1189px;
    height: 1200px;
    overflow: hidden;
    background: var(--backdrop);
    font-family: "Ubuntu", sans-serif;
  }
  .canvas { position: relative; width: 1189px; height: 1200px; }
  .card {
    position: absolute;
    left: 171px;
    width: 855px;
    height: 488px;
    overflow: hidden;
    box-shadow: 8px 10px 14px rgba(0,0,0,0.6);
  }
  .card--front {
    top: 67px;
    background:
      radial-gradient(circle at 82% 0%, var(--cyan) 0%, rgba(4,170,201,0) 55%),
      linear-gradient(35deg, var(--indigo) 0%, var(--brand-blue) 50%, #1a9cc6 100%);
  }
  .card--front .sheen { position: absolute; inset: 0; }
  .front-wordmark {
    position: absolute;
    left: 0; right: 0;
    top: 150px;
    text-align: center;
    color: var(--paper);
    font-weight: 500;
    font-size: 150px;
    letter-spacing: -4px;
    line-height: 1;
  }
  .card--back { top: 626px; background: var(--paper); }
  .card--back .swoosh { position: absolute; inset: 0; }
  .back-brand {
    position: absolute;
    left: 40px;
    top: 52px;
    display: flex;
    align-items: flex-start;
    gap: 8px;
  }
  .back-wordmark {
    color: var(--navy);
    font-weight: 500;
    font-size: 112px;
    letter-spacing: -3px;
    line-height: 1;
  }
  .brand-dot {
    width: 18px; height: 18px;
    border-radius: 50%;
    background: var(--green);
    margin-top: 16px;
  }
  .contact { position: absolute; left: 40px; top: 230px; color: var(--ink); }
  .contact .name { color: var(--navy); font-size: 30px; font-weight: 500; line-height: 32px; }
  .contact .title { font-size: 23px; line-height: 24px; }
  .contact .address { font-size: 23px; line-height: 26px; margin-top: 24px; }
  .contact .lines { list-style: none; margin-top: 18px; }
  .contact .lines li {
    font-size: 24px;
    line-height: 27px;
    display: flex;
    align-items: center;
    gap: 10px;
  }
  .contact .lines svg { width: 20px; height: 18px; flex: none; }
</style>
</head>
<body>
<div class="canvas">

  <section class="card card--front">
    <svg class="sheen" viewBox="0 0 855 488" preserveAspectRatio="none" aria-hidden="true">
      <path d="M160,0 C210,230 330,400 460,488 L855,488 L855,0 Z" fill="#ffffff" opacity="0.05"/>
    </svg>
    <div class="front-wordmark">orvel</div>
  </section>

  <section class="card card--back">
    <svg class="swoosh" viewBox="0 0 855 488" preserveAspectRatio="none" aria-hidden="true">
      <defs>
        <linearGradient id="blueArc" x1="0" y1="0" x2="1" y2="0">
          <stop offset="0" stop-color="#3a4aa8"/>
          <stop offset="0.5" stop-color="#30348f"/>
          <stop offset="1" stop-color="#2e3192"/>
        </linearGradient>
        <linearGradient id="greenArc" x1="0" y1="1" x2="0.6" y2="0">
          <stop offset="0" stop-color="#3db54a"/>
          <stop offset="1" stop-color="#b5d89a"/>
        </linearGradient>
      </defs>
      <path d="M691,0 C745,60 778,150 766,262 C756,360 722,430 690,488 L855,488 L855,0 Z" fill="url(#blueArc)"/>
      <path d="M518,488 C640,452 742,380 759,229 C753,350 718,432 676,488 Z" fill="url(#greenArc)"/>
    </svg>

    <div class="back-brand">
      <div class="back-wordmark">orvel</div>
      <span class="brand-dot"></span>
    </div>

    <div class="contact">
      <p class="name">Marcus Halloway</p>
      <p class="title">President</p>
      <p class="address">2410 W. Elm Ave Corvella, CA 91802</p>
      <ul class="lines">
        <li>
          <svg viewBox="0 0 20 18" aria-hidden="true"><path d="M1,6 C4,1 16,1 19,6 L16,8 L14,5 L6,5 L4,8 Z M4,10 L16,10 L18,17 L2,17 Z" fill="#2e3192"/><circle cx="10" cy="13" r="2" fill="#fff"/></svg>
          555-014-2288
        </li>
        <li>
          <svg viewBox="0 0 20 18" aria-hidden="true"><rect x="5" y="1" width="10" height="5" fill="#2e3192"/><rect x="1" y="6" width="18" height="8" rx="1" fill="#2e3192"/><rect x="5" y="11" width="10" height="6" fill="#2e3192" stroke="#fff" stroke-width="1"/></svg>
          555-014-2277
        </li>
        <li>
          <svg viewBox="0 0 20 18" aria-hidden="true"><rect x="5" y="0" width="10" height="18" rx="2" fill="#2e3192"/><rect x="7" y="2" width="6" height="5" fill="#fff"/><rect x="7" y="9" width="6" height="7" fill="#8f92d0"/></svg>
          555 017 4391
        </li>
        <li>
          <svg viewBox="0 0 20 18" aria-hidden="true"><rect x="1" y="3" width="18" height="13" fill="#2e3192"/><path d="M1,3 L10,11 L19,3 M1,16 L8,9 M19,16 L12,9" stroke="#fff" stroke-width="1.2" fill="none"/></svg>
          marcus@orvelpantry.com
        </li>
      </ul>
    </div>
  </section>

</div>
</body>
</html>
```